Corporate travel agency website design

Hello I need a website design that will look professional. I want that anyone that gos on our site understands that we are a large successful company. I want it to be up to par with other large companies. The site should be sleek and neat.
Below I will attach my logo. A recent one page add I made and content for my add that will be used for the website.

```html
<!DOCTYPE html>
<html lang="en">
<head>
<meta charset="UTF-8">
<title>Vantage Voyages – Business Travel</title>
<link href="https://fonts.googleapis.com/css2?family=Jost:wght@500;600;700&family=Questrial&display=swap" rel="stylesheet">
<style>
:root{
  --navy:#0b1f3e;
  --navy-deep:#081833;
  --ink:#111111;
  --white:#ffffff;
  --sky:#cdeefa;
  --sky-text:#bfe7f6;
  --field:#ffffff;
  --muted:#d9dde2;
  --footer:#000000;
}
*{box-sizing:border-box;margin:0;padding:0}
html,body{width:1200px;height:3075px;overflow:hidden}
body{position:relative;background:var(--white);font-family:"Questrial",sans-serif;color:var(--ink)}
.abs{position:absolute}
.heading{font-family:"Jost",sans-serif;font-weight:600;color:var(--ink);text-align:center;left:0;width:1200px}

/* nav */
.nav{top:0;left:0;width:1200px;height:86px;background:var(--white);z-index:3}
.nav-link{top:26px;font-size:17px;color:var(--ink);text-decoration:none}
.login{left:979px;top:13px;width:109px;height:42px;background:var(--navy);color:var(--white);border-radius:5px;font-family:"Jost",sans-serif;font-weight:600;font-size:14px;display:flex;align-items:center;justify-content:center}
.brand-badge{width:156px;height:156px;border-radius:50%;background:var(--navy);display:flex;align-items:center;justify-content:center;text-align:center;color:var(--white);font-family:"Questrial",sans-serif;font-size:15px;letter-spacing:1.5px;line-height:1.3;z-index:4}

/* hero */
.hero-photo{top:86px;left:0;width:1200px;height:600px;background:linear-gradient(100deg,#c9d4dc 0%,#dfe6ea 35%,#bfc9cf 55%,#c8b45a 62%,#9aa3a8 75%,#b7c7d2 100%)}
.hero-edge{top:0;left:0;z-index:2}
.welcome{left:111px;top:254px;font-family:"Jost",sans-serif;font-weight:500;font-size:31px;color:var(--sky-text)}
.hero-title{left:108px;top:290px;font-family:"Jost",sans-serif;font-weight:700;font-size:74px;color:var(--white);letter-spacing:1px}
.btn{background:var(--navy);color:var(--white);border-radius:5px;font-family:"Jost",sans-serif;font-weight:600;display:flex;align-items:center;justify-content:center}
.get-started{left:111px;top:398px;width:154px;height:52px;font-size:16px}
.hero-dots{top:529px;left:485px;display:flex;gap:11px}
.hero-dots span{width:37px;height:3px;background:var(--white)}
.hero-dots span.on{background:#9fdcf2}
.round-badge{width:72px;height:72px;border-radius:50%;background:var(--white);border:3px solid #d5eef8;box-shadow:0 4px 14px rgba(0,0,0,.18);display:flex;align-items:center;justify-content:center;z-index:3}

/* services */
.card{overflow:hidden}
.card-photo{width:100%;height:100%}
.card-label{position:absolute;left:0;width:100%;text-align:center;font-family:"Jost",sans-serif;font-weight:600;font-size:25px;color:var(--white)}
.circle-arrow{width:40px;height:40px;border-radius:50%;background:var(--sky);display:flex;align-items:center;justify-content:center;z-index:2}
.card-featured{left:447px;top:819px;width:290px;height:387px;background:linear-gradient(160deg,#123458,#0b2647);color:var(--white);text-align:center}
.card-featured h3{font-family:"Jost",sans-serif;font-weight:600;font-size:25px;line-height:29px;margin-top:100px}
.card-featured p{font-size:17.5px;line-height:28.5px;margin:20px 20px 0}
.slider-bars{top:1246px;left:427px;display:flex;gap:15px}
.slider-bars span{width:57px;height:4px;background:#e3e6ea;border-radius:2px}
.slider-bars span.on{background:var(--navy)}

/* why */
.why-bg{top:1337px;left:0;width:1200px;height:727px;background:linear-gradient(180deg,#ffffff 0%,#e9eef1 18%,#d5e0e4 42%,#7fbcc6 62%,#3e9aa8 80%,#2d8493 100%)}
.why-text{left:170px;top:1472px;width:860px;font-size:16.6px;line-height:25.7px;text-align:center;color:#1b1b1b}
.learn-more{left:525px;top:1705px;width:150px;height:53px;font-size:16px}

/* contact */
.field{background:var(--field);box-shadow:0 6px 18px rgba(0,0,0,.06);font-size:19px;color:#333;padding:22px 0 0 24px}

/* footer */
.footer{top:2690px;left:0;width:1200px;height:385px}
.map-shade{top:2800px;left:300px;width:620px;height:275px;background:radial-gradient(ellipse at center,#1a1a1a 0%,#0b0b0b 60%,rgba(0,0,0,0) 100%);z-index:1}
.foot-link{top:2885px;font-size:17px;color:var(--white);z-index:2}
.foot-rule{left:110px;top:2952px;width:980px;height:1px;background:#2c2c2c;z-index:2}
.copyright{left:112px;top:2995px;font-size:16.5px;color:var(--white);z-index:2}
.social{top:2990px;width:30px;height:30px;border-radius:50%;background:#2a2a2a;z-index:2}
.social.first{background:var(--white)}
</style>
</head>
<body>

<!-- hero imagery -->
<div class="abs hero-photo" role="img" aria-label="Airport lounge with two suitcases by a window and a plane taking off"></div>
<svg class="abs hero-edge" width="1200" height="700" viewBox="0 0 1200 700" aria-hidden="true">
  <polygon points="0,645 1200,528 1200,545 0,684" fill="#0b1f3e"/>
  <polygon points="0,684 1200,545 1200,700 0,700" fill="#ffffff"/>
</svg>

<!-- navigation -->
<header class="abs nav">
  <a class="abs nav-link" style="left:551px" href="#">Home</a>
  <a class="abs nav-link" style="left:643px" href="#">About</a>
  <a class="abs nav-link" style="left:737px" href="#">Services</a>
  <a class="abs nav-link" style="left:844px" href="#">Contact</a>
  <div class="abs login">LOGIN</div>
</header>
<div class="abs brand-badge" style="left:109px;top:9px">VANTAGE<br>VOYAGES</div>

<div class="abs welcome">Welcome To</div>
<div class="abs hero-title">VANTAGE VOYAGES</div>
<div class="abs btn get-started">Get Started</div>
<div class="abs hero-dots"><span></span><span></span><span class="on"></span><span></span><span></span></div>

<div class="abs round-badge" style="left:564px;top:575px">
  <svg width="26" height="26" viewBox="0 0 24 24" aria-hidden="true"><path d="M12 4v16M5 13l7 7 7-7" stroke="#0b1f3e" stroke-width="2.6" fill="none" stroke-linecap="round" stroke-linejoin="round"/></svg>
</div>

<!-- services -->
<h2 class="abs heading" style="top:732px;font-size:41px">Our Services</h2>

<div class="abs card" style="left:171px;top:841px;width:258px;height:345px;clip-path:polygon(0 0,100% 0,100% 100%,0 97%)">
  <div class="card-photo" role="img" aria-label="Two travellers reading a map in an old town" style="background:linear-gradient(180deg,#d8cfc4 0%,#b89f86 45%,#6f8794 75%,#2f4a63 100%)"></div>
  <div class="card-label" style="top:266px">Unparalled Service</div>
</div>
<div class="abs circle-arrow" style="left:278px;top:1163px">
  <svg width="16" height="16" viewBox="0 0 24 24" aria-hidden="true"><path d="M12 4v16M5 13l7 7 7-7" stroke="#0b1f3e" stroke-width="2.6" fill="none" stroke-linecap="round" stroke-linejoin="round"/></svg>
</div>

<div class="abs card card-featured">
  <div class="abs circle-arrow" style="left:120px;top:42px">
    <svg width="16" height="16" viewBox="0 0 24 24" aria-hidden="true"><path d="M12 20V4M5 11l7-7 7 7" stroke="#0b1f3e" stroke-width="2.6" fill="none" stroke-linecap="round" stroke-linejoin="round"/></svg>
  </div>
  <h3>Budget and Travel<br>Spend Reporting</h3>
  <p>Having a travel management service will ensure that your company enforces corporate compliance and maintains control over travel</p>
</div>

<div class="abs card" style="left:755px;top:841px;width:257px;height:345px;clip-path:polygon(0 0,100% 0,100% 100%,0 97%)">
  <div class="card-photo" role="img" aria-label="Hiker looking over misty mountains at sunset" style="background:linear-gradient(180deg,#e8c594 0%,#b9a085 30%,#6f7563 60%,#2c3f55 100%)"></div>
  <div class="card-label" style="top:262px">Efficiency</div>
</div>
<div class="abs circle-arrow" style="left:859px;top:1163px">
  <svg width="16" height="16" viewBox="0 0 24 24" aria-hidden="true"><path d="M12 4v16M5 13l7 7 7-7" stroke="#0b1f3e" stroke-width="2.6" fill="none" stroke-linecap="round" stroke-linejoin="round"/></svg>
</div>

<div class="abs slider-bars"><span></span><span></span><span class="on"></span><span></span><span></span></div>

<!-- why choose -->
<div class="abs why-bg" role="img" aria-label="Two backpackers by a turquoise mountain lake"></div>
<h2 class="abs heading" style="top:1403px;font-size:40px">Why Choose Vantage Voyages?</h2>
<p class="abs why-text">Vantage Voyages is a global leader in business travel management services. We drive savings, efficiency, and unparalleled service to businesses and their travelers all around the world. If you are looking for a tailored travel managed solution focused on offering white glove service and fulfilling your individual preferences ,while delivering customer excellence, you’ve come to the right place. At Vantage Voyages, our mission is to have you focus on your day to day business while we handle all of the logistics and details for the most successful all encompassing travel experience. From emergency passport arrangements to last minute cancellations, re-bookings, and other intricate travel challenges, Vantage Voyages is well versed in handling the routine array of travel services, as well as solving any travel related issue that might arise.</p>
<div class="abs btn learn-more">Learn More</div>

<!-- contact -->
<h2 class="abs heading" style="top:2142px;font-size:47px">Contact Us</h2>
<div class="abs field" style="left:115px;top:2246px;width:472px;height:61px">First Name</div>
<div class="abs field" style="left:608px;top:2246px;width:473px;height:61px">Last Name</div>
<div class="abs field" style="left:115px;top:2327px;width:472px;height:62px">Email</div>
<div class="abs field" style="left:608px;top:2327px;width:473px;height:62px">Phone</div>
<div class="abs field" style="left:115px;top:2412px;width:968px;height:128px;padding-top:26px">How Can We Help?</div>
<div class="abs btn" style="left:515px;top:2589px;width:169px;height:53px;font-size:20px">Submit</div>

<!-- footer -->
<svg class="abs footer" width="1200" height="385" viewBox="0 0 1200 385" aria-hidden="true">
  <polygon points="0,146 1200,9 1200,385 0,385" fill="#0b1f3e"/>
  <polygon points="0,146 1200,33 1200,385 0,385" fill="#000000"/>
</svg>
<div class="abs map-shade" role="img" aria-label="Dotted world map"></div>
<div class="abs round-badge" style="left:564px;top:2729px">
  <svg width="26" height="26" viewBox="0 0 24 24" aria-hidden="true"><path d="M12 20V4M5 11l7-7 7 7" stroke="#0b1f3e" stroke-width="2.6" fill="none" stroke-linecap="round" stroke-linejoin="round"/></svg>
</div>
<div class="abs brand-badge" style="left:926px;top:2765px">VANTAGE<br>VOYAGES</div>
<a class="abs foot-link" style="left:110px">Home</a>
<a class="abs foot-link" style="left:203px">About</a>
<a class="abs foot-link" style="left:296px">Services</a>
<a class="abs foot-link" style="left:403px">Contact</a>
<div class="abs foot-rule"></div>
<div class="abs copyright">©Copyrights 2023 Vantage Voyages. &nbsp;| &nbsp;&nbsp; All Rights Reserved</div>
<span class="abs social first" style="left:951px"></span>
<span class="abs social" style="left:988px"></span>
<span class="abs social" style="left:1024px"></span>
<span class="abs social" style="left:1060px"></span>

</body>
</html>
```